Manuka Honey company needs a Upmarket, Luxury Website!

New Zealand, Taranaki based Manuka Honey company Rimu Vale Honey is looking for a new website, we are looking for an upmarket, luxury, serious website design. We export the highest quality quality Manuka Honey, straight from the Taranaki region.

Main export markets are Asia & Europe, also New Zealand & Australia.

Looking to have a beautiful, upmarket, serious, luxurious & graphical experience with mobile optimization in mind. Like the use of product staging/mockups

You can use copy from other websites to build the site and we will change the copy after the design is finished.

***Please include 'Honey Product' mockups in website.

*Will add illustrator files in coming days***

Feel free to make website functional in Shopify, Wordpress or WIX

Target Market(s)

Asia, Europe (main markets) New Zealand, Australia (Submarkets)

Coding

Coded - Design and coding required

Number of Pages Required

4 page

Requirements
Must have
• Home, Shop, About Us, Contact Us

Homepage to include:

Our Products
Company Video (video under construction)
What is MGO/KPS
Newsletter Opt-in

***(Not in Order)***

Please include 'Honey Product' mockups in website.
*Will add illustrator files in coming days
Nice to have
• FAQ & Partnership Inquiries (hyperlink in footer)

```html
<!DOCTYPE html>
<html lang="en">
<head>
<meta charset="utf-8">
<title>Rimu Vale Honey — Quality Manuka Honey</title>
<link rel="stylesheet" href="https://fonts.googleapis.com/css2?family=Montserrat:wght@400;500;600;700;800&family=Nunito+Sans:wght@300;400;600;700&display=swap">
<style>
:root{
  --black:#000;
  --ink:#151515;
  --text:#555;
  --gold:#e3a21c;
  --gold-light:#f0c23a;
  --gold-dark:#c98610;
  --sand:#e6cf82;
  --brown:#6a3d13;
  --green:#3a8a1e;
  --white:#fff;
  --grey:#f3f1f2;
}
*{box-sizing:border-box;margin:0;padding:0}
html,body{width:1200px;height:4216px;overflow:hidden}
body{position:relative;font-family:"Nunito Sans",Arial,sans-serif;color:var(--ink);background:var(--white)}
.abs{position:absolute}
.heading{font-family:"Montserrat",Arial,sans-serif;font-weight:700}

/* header */
.site-header{left:0;top:0;width:1200px;height:98px;background:var(--black)}
.brand{left:95px;top:30px;display:flex;align-items:center;gap:14px}
.brand-dot{width:36px;height:36px;border-radius:50%;border:2px solid var(--gold)}
.brand-name{font-family:"Montserrat",sans-serif;font-weight:500;font-size:26px;letter-spacing:4px;color:var(--gold)}
.main-nav a{position:absolute;top:43px;font-family:"Montserrat",sans-serif;font-size:13px;color:var(--gold);text-decoration:none;letter-spacing:.5px}
.main-nav a.active{color:var(--white);font-weight:700}

/* hero */
.hero{left:0;top:98px;width:1200px;height:720px;background:linear-gradient(120deg,#8fa64a 0%,#c7d49a 35%,#6f8a33 65%,#a8b876 100%)}
.hero-badge{left:82px;top:124px;width:426px;height:426px;border-radius:50%;background:radial-gradient(circle at 40% 35%,#eab52a,#d99312);text-align:center;color:var(--white)}
.hero-badge .badge-dot{width:46px;height:46px;border-radius:50%;border:2px solid rgba(255,255,255,.8);margin:62px auto 0}
.hero-badge .kicker{font-size:28px;font-weight:600;margin-top:20px}
.hero-badge h1{font-family:"Montserrat",sans-serif;font-weight:800;font-size:40px;line-height:47px;margin-top:6px}
.btn-hero{display:inline-flex;align-items:center;gap:10px;margin-top:22px;width:171px;height:49px;justify-content:center;border-radius:25px;background:var(--brown);color:var(--white);font-family:"Montserrat",sans-serif;font-weight:700;font-size:13px}
.slider-dots{left:572px;top:682px;display:flex;gap:13px}
.slider-dots span{width:12px;height:12px;border-radius:50%;border:2px solid var(--white)}
.slider-dots span.on{background:var(--white)}
.hero-wave{left:0;top:660px;width:1200px;height:160px}

/* about */
.eyebrow{font-size:24px;font-weight:300;color:var(--gold)}
.section-title{font-family:"Montserrat",sans-serif;font-weight:800;color:var(--ink)}
.rule{height:3px;background:var(--green)}
.about-eyebrow{left:139px;top:911px}
.about-title{left:139px;top:942px;font-size:35px}
.about-rule{left:139px;top:990px;width:65px}
.about-copy{left:139px;top:1016px;width:400px;font-size:12px;line-height:23.5px;color:var(--text)}
.about-copy p+p{margin-top:22px}
.btn-outline{left:134px;top:1200px;width:146px;height:41px;border:2px solid var(--gold);border-radius:21px;color:var(--gold);font-family:"Montserrat",sans-serif;font-weight:600;font-size:11px;display:flex;align-items:center;justify-content:center;gap:8px}
.orbit{left:660px;top:876px;width:392px;height:392px;border-radius:50%;border:2px dashed #cfcfcf}
.about-art{left:704px;top:930px;width:306px;height:273px;border-radius:50% 50% 45% 45%;background:radial-gradient(circle,#f3e3a8,#e1c060 60%,#fff 75%)}
.orbit-icon{width:72px;height:72px;border-radius:50%;background:var(--white);box-shadow:0 4px 14px rgba(0,0,0,.12);display:flex;align-items:center;justify-content:center}
.orbit-icon span{width:28px;height:28px;border-radius:50%;border:2px solid var(--gold)}

/* products */
.products-band{left:0;top:1358px;width:1200px;height:444px;background:linear-gradient(180deg,#ebe6ea 0%,#d9cfd3 45%,#c8b79a 80%,#b9a884 100%)}
.products-eyebrow{left:0;top:1410px;width:1200px;text-align:center;font-size:21px;font-weight:400;color:#333}
.products-title{left:0;top:1442px;width:1200px;text-align:center;font-size:32px}
.products-rule{left:569px;top:1487px;width:62px}
.product-card{top:1545px;width:226px;height:346px;background:var(--white);box-shadow:0 2px 10px rgba(0,0,0,.08);text-align:center}
.product-jar{width:84px;height:155px;margin:35px auto 0;border-radius:14px 14px 10px 10px;background:linear-gradient(180deg,#2b2b2b 0 9%,#d08a22 9% 18%,#2f2f2f 18% 88%,#c27a1a 88%)}
.product-name{margin-top:30px;font-family:"Montserrat",sans-serif;font-weight:500;font-size:15px}
.product-price{margin-top:6px;font-family:"Montserrat",sans-serif;font-weight:600;font-size:13px}
.product-price .stars{color:var(--gold);letter-spacing:1px;font-size:11px;margin-right:4px}
.btn-small{display:inline-flex;align-items:center;justify-content:center;margin-top:18px;width:120px;height:30px;border-radius:15px;background:linear-gradient(90deg,#caa86a,#f1dc8c);font-family:"Montserrat",sans-serif;font-weight:700;font-size:8.5px;letter-spacing:1px;color:#3b2a12}

/* why choose */
.why-title{left:0;top:1978px;width:1168px;text-align:center;font-size:33px}
.why-rule{left:560px;top:2029px;width:62px}
.why-ring{left:159px;top:2102px;width:458px;height:458px;border-radius:50%;border:2px solid #e6e6e6}
.ring-dot{width:12px;height:12px;border-radius:50%;background:var(--sand)}
.why-art{left:187px;top:2130px;width:402px;height:402px;border-radius:50%;background:radial-gradient(circle at 45% 40%,#f5c95a,#e4a11c 70%)}
.why-jar{width:118px;height:210px;border-radius:18px 18px 14px 14px;background:linear-gradient(180deg,#262626 0 10%,#e0a12d 10% 35%,#2b2b2b 35% 85%,#c5801a 85%)}
.feature-icon{width:80px;height:80px;border-radius:50%;border:1px solid #e2e2e2;background:var(--white);display:flex;align-items:center;justify-content:center}
.feature-icon span{width:30px;height:30px;border-radius:50%;border:2px solid var(--gold)}
.feature-label{font-family:"Montserrat",sans-serif;font-size:15px;letter-spacing:2px;color:#222}
.feature-name{font-family:"Montserrat",sans-serif;font-weight:700;font-size:15px;letter-spacing:2px;color:#111}
.feature-desc{font-size:12px;color:var(--text);margin-top:4px;white-space:nowrap}

/* video */
.video-band{left:0;top:2701px;width:1200px;height:516px;background:linear-gradient(110deg,#3c4a32 0%,#55634a 40%,#7d8478 70%,#4a5240 100%)}
.video-title{left:157px;top:2905px;font-size:31px;color:var(--white)}
.video-sub{left:161px;top:2953px;font-size:16px;color:var(--white)}
.video-line{left:660px;top:2929px;width:159px;height:1px;background:rgba(255,255,255,.6)}
.play{left:850px;top:2892px;width:76px;height:76px}

/* contact */
.contact-band{left:0;top:3217px;width:1200px;height:600px;background:linear-gradient(120deg,#6b7a3f 0%,#c9a86c 30%,#b7b39b 55%,#6f7560 100%)}
.contact-title{left:676px;top:3314px;font-size:29px;color:var(--white)}
.contact-rule{left:676px;top:3356px;width:60px;background:var(--white)}
.field{left:674px;width:408px;background:var(--white);font-size:12px;color:#555;padding:0 17px;display:flex;align-items:center}
.field.area{align-items:flex-start;padding-top:14px}
.btn-send{left:674px;top:3624px;width:159px;height:43px;border-radius:22px;background:linear-gradient(90deg,#d88c0e,#f0b72a);color:var(--white);font-family:"Montserrat",sans-serif;font-weight:700;font-size:11px;letter-spacing:1.5px;display:flex;align-items:center;justify-content:center}
.footer-wave{left:0;top:3660px;width:1200px;height:160px}

/* footer */
.site-footer{left:0;top:3818px;width:1200px;height:398px;background:var(--black)}
.footer-mark{left:152px;top:3868px;width:170px;height:170px;border-radius:50%;border:2px solid var(--gold);display:flex;align-items:center;justify-content:center;text-align:center;color:var(--gold);font-family:"Montserrat",sans-serif;font-weight:600;font-size:15px;letter-spacing:2px;line-height:22px}
.footer-col h3{font-family:"Montserrat",sans-serif;font-weight:700;font-size:14px;letter-spacing:2px;color:var(--white)}
.footer-col .rule{width:30px;height:2px;background:var(--gold);margin-top:6px}
.footer-col ul{list-style:none;margin-top:20px}
.footer-col li{font-size:11.5px;color:var(--white);height:28px}
.news-text{font-size:12px;color:var(--white);margin-top:20px}
.news-input{margin-top:12px;width:224px;height:33px;border-radius:17px;background:var(--white);font-size:11px;color:#555;padding-left:20px;display:flex;align-items:center}
.news-btn{margin-top:11px;width:224px;height:33px;border-radius:17px;background:linear-gradient(90deg,#d88c0e,#f0b72a);color:var(--white);font-family:"Montserrat",sans-serif;font-weight:700;font-size:12px;display:flex;align-items:center;justify-content:center}
.social{display:flex;gap:20px;margin-top:16px}
.social span{width:14px;height:14px;border-radius:50%;background:var(--white)}
.footer-divider{left:0;top:4142px;width:1200px;height:1px;background:#222}
.copyright{left:0;top:4162px;width:1200px;text-align:center;font-size:10px;color:#bbb}
</style>
</head>
<body>

<header class="site-header abs">
  <div class="brand abs"><span class="brand-dot"></span><span class="brand-name">RIMU VALE HONEY</span></div>
  <nav class="main-nav">
    <a class="active" style="left:573px">HOME</a>
    <a style="left:704px">SHOP</a>
    <a style="left:823px">ABOUT US</a>
    <a style="left:972px">CONTACT US</a>
  </nav>
</header>

<section class="hero abs" role="img" aria-label="Close-up photograph of white manuka blossoms on a branch against soft green foliage">
  <div class="hero-badge abs">
    <div class="badge-dot"></div>
    <div class="kicker">Specialize in</div>
    <h1>SELLING QUALITY<br>MANUKA&nbsp; HONEY</h1>
    <div class="btn-hero">VIEW HONEY <span>&#8250;</span></div>
  </div>
  <div class="slider-dots abs"><span class="on"></span><span></span><span></span></div>
</section>
<svg class="hero-wave abs" viewBox="0 0 1200 160" preserveAspectRatio="none" aria-hidden="true">
  <path d="M0 50 C250 100 500 110 760 60 C950 22 1100 30 1200 80 L1200 160 L0 160Z" fill="#e8d37e"/>
  <path d="M0 80 C260 140 520 130 780 80 C960 45 1100 60 1200 110 L1200 160 L0 160Z" fill="#fff"/>
  <path d="M0 92 C260 160 520 150 790 95 C970 58 1110 70 1200 118 L1200 132 C1110 90 970 82 790 118 C520 172 260 175 0 112Z" fill="#e5a91f"/>
  <path d="M0 118 C260 182 520 175 790 125 C970 92 1110 100 1200 140 L1200 160 L0 160Z" fill="#fff"/>
</svg>

<section class="about">
  <p class="eyebrow about-eyebrow abs">Who We Are</p>
  <h2 class="section-title about-title abs">ABOUT RIMU VALE HONEY</h2>
  <div class="rule about-rule abs"></div>
  <div class="about-copy abs">
    <p>Curabitur vel dolor ultrices ipsum dictum tristique Praesent vitae lacus Ut velit enim vestibulum non fermentum nec hendrerit quis leo Pellentesque rutrum malesuada neque Nunc tempus felis vitae urna Vivamus porttitor neque at volutpat rutrum purus nisi</p>
    <p>Morbi diam mauris viverra in gravida eu mattis in anquam Curabitur vel dolor ultrices ipsum dictum tristique Praesent vita</p>
  </div>
  <div class="btn-outline abs">LEARN MORE <span>&#8250;</span></div>
  <div class="orbit abs"></div>
  <div class="about-art abs" role="img" aria-label="Ornamental golden bee illustration with blue and green inlay"></div>
  <div class="orbit-icon abs" style="left:648px;top:917px"><span></span></div>
  <div class="orbit-icon abs" style="left:984px;top:904px"><span></span></div>
  <div class="orbit-icon abs" style="left:640px;top:1103px"><span></span></div>
  <div class="orbit-icon abs" style="left:987px;top:1087px"><span></span></div>
  <div class="orbit-icon abs" style="left:820px;top:1216px"><span></span></div>
</section>

<section class="products">
  <div class="products-band abs" role="img" aria-label="Misty landscape photograph of a snow-capped volcano above golden grassland"></div>
  <p class="products-eyebrow abs">Show Now</p>
  <h2 class="section-title products-title abs">OUR PRODUCTS</h2>
  <div class="rule products-rule abs"></div>

  <article class="product-card abs" style="left:121px">
    <div class="product-jar" role="img" aria-label="Jar of manuka honey with black label"></div>
    <h3 class="product-name">Tawari Gold Honey</h3>
    <p class="product-price"><span class="stars">★★★★★</span>USD $18.00</p>
    <span class="btn-small">LEARN MORE</span>
  </article>
  <article class="product-card abs" style="left:367px">
    <div class="product-jar" role="img" aria-label="Jar of light manuka honey with black label"></div>
    <h3 class="product-name">Tawari Gold Honey</h3>
    <p class="product-price"><span class="stars">★★★★★</span>USD $18.00</p>
    <span class="btn-small">LEARN MORE</span>
  </article>
  <article class="product-card abs" style="left:612px">
    <div class="product-jar" role="img" aria-label="Jar of amber manuka honey with black label"></div>
    <h3 class="product-name">Tawari Gold Honey</h3>
    <p class="product-price"><span class="stars">★★★★★</span>USD $18.00</p>
    <span class="btn-small">LEARN MORE</span>
  </article>
  <article class="product-card abs" style="left:861px">
    <div class="product-jar" role="img" aria-label="Jar of dark manuka honey with black label"></div>
    <h3 class="product-name">Tawari Gold Honey</h3>
    <p class="product-price"><span class="stars">★★★★★</span>USD $18.00</p>
    <span class="btn-small">LEARN MORE</span>
  </article>
</section>

<section class="why">
  <h2 class="section-title why-title abs">Why Choose MGO</h2>
  <div class="rule why-rule abs"></div>
  <div class="why-ring abs"></div>
  <div class="why-art abs" role="img" aria-label="Golden honey background with white ornamental bee line art"></div>
  <div class="why-jar abs" style="left:444px;top:2374px" role="img" aria-label="Jar of manuka honey"></div>
  <div class="why-jar abs" style="left:360px;top:2415px;height:180px" role="img" aria-label="Jar of manuka honey"></div>
  <span class="ring-dot abs" style="left:534px;top:2152px"></span>
  <span class="ring-dot abs" style="left:598px;top:2245px"></span>
  <span class="ring-dot abs" style="left:610px;top:2346px"></span>
  <span class="ring-dot abs" style="left:578px;top:2446px"></span>

  <div class="feature-icon abs" style="left:569px;top:2085px"><span></span></div>
  <div class="abs" style="left:668px;top:2084px">
    <p class="feature-label">CERTIFIED KPS</p><p class="feature-name">SUPER PREIMUM</p>
    <p class="feature-desc">Lorem ipsum dolor sit amet, consectetur adipiscing elit, sed do ei</p>
  </div>
  <div class="feature-icon abs" style="left:648px;top:2203px"><span></span></div>
  <div class="abs" style="left:740px;top:2202px">
    <p class="feature-label">CERTIFIED KPS</p><p class="feature-name">ULTRA PREIMUM</p>
    <p class="feature-desc">Lorem ipsum dolor sit amet, consectetur adipiscing elit, se</p>
  </div>
  <div class="feature-icon abs" style="left:661px;top:2324px"><span></span></div>
  <div class="abs" style="left:750px;top:2328px">
    <p class="feature-label">CERTIFIED KPS</p><p class="feature-name">SUPER PREIMUM</p>
    <p class="feature-desc">Lorem ipsum dolor sit amet, consectetur adipiscing elit,</p>
  </div>
  <div class="feature-icon abs" style="left:615px;top:2445px"><span></span></div>
  <div class="abs" style="left:712px;top:2465px">
    <p class="feature-label">CERTIFIED KPS</p><p class="feature-name">SUPER PREIMUM</p>
    <p class="feature-desc">Lorem ipsum dolor sit amet, consectetur adipiscing elit,</p>
  </div>
</section>

<section class="video">
  <div class="video-band abs" role="img" aria-label="Darkened photograph of a beekeeper in protective suit inspecting hive frames in a field"></div>
  <h2 class="heading video-title abs">WATCH OUR COMPANY VIDEO</h2>
  <p class="video-sub abs">Lorem ipsum dolor sit amet, consectetur adipiscing</p>
  <div class="video-line abs"></div>
  <svg class="play abs" viewBox="0 0 76 76" aria-label="Play video">
    <circle cx="38" cy="38" r="34" fill="none" stroke="#fff" stroke-width="5"/>
    <path d="M30 24 L54 38 L30 52Z" fill="#fff"/>
  </svg>
</section>

<section class="contact">
  <div class="contact-band abs" role="img" aria-label="Close-up photograph of a honey bee on a white manuka flower"></div>
  <h2 class="heading contact-title abs">STAY IN TOUCH WITH US</h2>
  <div class="rule contact-rule abs"></div>
  <div class="field abs" style="top:3382px;height:43px">Name*</div>
  <div class="field abs" style="top:3434px;height:42px">E-mail*</div>
  <div class="field abs" style="top:3487px;height:42px">Phone number*</div>
  <div class="field area abs" style="top:3539px;height:71px">Type Message</div>
  <div class="btn-send abs">SEND MESSAGE</div>
</section>
<svg class="footer-wave abs" viewBox="0 0 1200 160" preserveAspectRatio="none" aria-hidden="true">
  <path d="M0 40 C200 10 420 30 640 55 C860 80 1050 40 1200 0 L1200 160 L0 160Z" fill="#e8d37e"/>
  <path d="M0 58 C200 30 420 48 640 72 C860 96 1050 58 1200 22 L1200 160 L0 160Z" fill="#e5a91f"/>
  <path d="M0 75 C200 50 420 68 640 92 C860 116 1050 80 1200 45 L1200 160 L0 160Z" fill="#000"/>
</svg>

<footer class="site-footer abs"></footer>
<div class="footer-mark abs">RIMU VALE<br>HONEY</div>
<div class="footer-col abs" style="left:399px;top:3874px">
  <h3>NAVIGATION</h3><div class="rule"></div>
  <ul><li>Home</li><li>About Us</li><li>Products</li><li>Videos</li><li>Contact Us</li></ul>
</div>
<div class="footer-col abs" style="left:606px;top:3874px">
  <h3>USEFUL LINKS</h3><div class="rule"></div>
  <ul><li>FAQ</li><li>Partnership Inquiries</li><li>Terms</li><li>Shipping &amp; Return</li><li>Cart</li></ul>
</div>
<div class="footer-col abs" style="left:845px;top:3874px">
  <h3>NEWSLETTER SIGN UP</h3>
  <p class="news-text">Sign up here to stay up to date</p>
  <div class="news-input">Email adress</div>
  <div class="news-btn">Subscribe</div>
  <div class="social" aria-label="Social media links"><span></span><span></span><span></span><span></span></div>
</div>
<div class="footer-divider abs"></div>
<p class="copyright abs">COPYRIGHT © 2021 RIMU VALE HONEY ALL RIGHT RESERVED</p>

</body>
</html>
```